Redesign of business card for Cedar Ridge Mechanical

We are looking for a new design for our business cards for Cedar Ridge Mechanical. We are a plumbing & HVAC construction company, operating on the West Coast of Canada and USA. Logo attached.
Industry/Entity Type
Construction - Plumbing & HVAC
Contact Information for Business Card
Name, address, phone numbers, email, website address
Look and feel
Each slider illustrates characteristics of the customer's brand and the style your logo design should communicate.

```html
<!DOCTYPE html>
<html lang="en">
<head>
<meta charset="UTF-8">
<title>Cedar Ridge Mechanical — Business Card</title>
<link rel="stylesheet" href="https://fonts.googleapis.com/css2?family=Poppins:wght@300;400;600&display=swap">
<style>
  :root {
    --canvas: #222223;
    --card: #1f1f21;
    --card-edge: #2a2a2d;
    --ink: #ffffff;
    --ink-soft: #d9d9db;
    --emboss: #2c2c30;
    --emboss-line: #38383d;
  }
  * { box-sizing: border-box; margin: 0; padding: 0; }
  html, body {
    width: 1200px; height: 780px; overflow: hidden;
    background: var(--canvas);
    font-family: "Poppins", sans-serif;
    color: var(--ink);
  }
  .stage {
    width: 1200px; height: 780px;
    display: flex; align-items: center; justify-content: center; gap: 40px;
  }
  .card {
    position: relative;
    width: 560px; height: 320px;
    background: var(--card);
    border: 1px solid var(--card-edge);
    border-radius: 4px;
    overflow: hidden;
  }
  /* front */
  .brand {
    position: absolute; left: 34px; top: 30px;
    display: flex; align-items: center; gap: 10px;
  }
  .brand-square {
    width: 26px; height: 26px; border: 3px solid var(--ink); border-radius: 4px;
  }
  .brand-name {
    font-size: 15px; font-weight: 600; letter-spacing: 0.5px; text-transform: uppercase;
    color: var(--ink);
  }
  .contact {
    position: absolute; left: 34px; top: 96px;
    font-size: 12.5px; font-weight: 300; line-height: 1.55; color: var(--ink-soft);
  }
  .contact .address { margin-bottom: 8px; }
  .contact-row { display: flex; align-items: center; gap: 8px; }
  .contact-row svg { width: 12px; height: 12px; fill: var(--ink); flex: none; }
  .person {
    position: absolute; right: 40px; top: 110px; text-align: right;
  }
  .person-name { font-size: 26px; font-weight: 300; line-height: 1.1; }
  .person-name strong { font-weight: 600; }
  .person-role { font-size: 14px; font-weight: 300; margin-top: 4px; color: var(--ink-soft); }
  .accent-bar {
    position: absolute; right: 0; top: 104px; width: 14px; height: 70px; background: var(--ink);
  }
  .watermark-name {
    position: absolute; right: 36px; bottom: 26px;
    font-size: 30px; font-weight: 600; text-transform: uppercase; letter-spacing: 1px;
    color: var(--emboss);
  }
  /* back */
  .card-back { display: flex; align-items: center; justify-content: center; }
  .back-brand { display: flex; align-items: center; gap: 16px; }
  .back-square {
    width: 44px; height: 44px; border: 5px solid var(--emboss-line); border-radius: 8px;
  }
  .back-name {
    font-size: 26px; font-weight: 600; text-transform: uppercase; letter-spacing: 1px;
    color: var(--emboss-line);
  }
</style>
</head>
<body>
<main class="stage">
  <section class="card card-front" aria-label="Card front">
    <div class="brand">
      <span class="brand-square"></span>
      <span class="brand-name">Cedar Ridge Mechanical</span>
    </div>
    <div class="contact">
      <p class="address">1840 Harbor Ln. Suite 310<br>Portland, OR 97205</p>
      <p class="contact-row">
        <svg viewBox="0 0 24 24" aria-hidden="true"><path d="M6.6 10.8a15 15 0 0 0 6.6 6.6l2.2-2.2c.3-.3.7-.4 1-.2 1.1.4 2.3.6 3.6.6.6 0 1 .4 1 1V20c0 .6-.4 1-1 1A17 17 0 0 1 3 4c0-.6.4-1 1-1h3.5c.6 0 1 .4 1 1 0 1.3.2 2.5.6 3.6.1.3 0 .7-.2 1z"/></svg>
        (503) 555-0148
      </p>
      <p class="contact-row">
        <svg viewBox="0 0 24 24" aria-hidden="true"><path d="M2 5h20v14H2zm2 2v.5l8 5 8-5V7zm0 3v7h16v-7l-8 5z"/></svg>
        info@cedarridgemech.com
      </p>
      <p class="contact-row">
        <svg viewBox="0 0 24 24" aria-hidden="true"><path d="M12 2a10 10 0 1 0 0 20 10 10 0 0 0 0-20zm6.9 6h-3a15 15 0 0 0-1.3-3.9A8 8 0 0 1 18.9 8zM12 4c.8 1.2 1.5 2.5 1.9 4h-3.8c.4-1.5 1.1-2.8 1.9-4zM4.3 14a8 8 0 0 1 0-4h3.4a16 16 0 0 0 0 4zm.8 2h3a15 15 0 0 0 1.3 3.9A8 8 0 0 1 5.1 16zm3-8h-3a8 8 0 0 1 4.3-3.9A15 15 0 0 0 8.1 8zM12 20c-.8-1.2-1.5-2.5-1.9-4h3.8c-.4 1.5-1.1 2.8-1.9 4zm2.3-6H9.7a14 14 0 0 1 0-4h4.6a14 14 0 0 1 0 4zm.3 5.9a15 15 0 0 0 1.3-3.9h3a8 8 0 0 1-4.3 3.9zm1.7-5.9a16 16 0 0 0 0-4h3.4a8 8 0 0 1 0 4z"/></svg>
        www.cedarridgemech.com
      </p>
    </div>
    <div class="person">
      <p class="person-name"><strong>Marta</strong> Kovalen</p>
      <p class="person-role">Founder &amp; CEO</p>
    </div>
    <span class="accent-bar"></span>
    <p class="watermark-name">Cedar Ridge Mechanical</p>
  </section>

  <section class="card card-back" aria-label="Card back">
    <div class="back-brand">
      <span class="back-square"></span>
      <span class="back-name">Cedar Ridge Mechanical</span>
    </div>
  </section>
</main>
</body>
</html>
```